Norvane Website Design (New Start Up Investment Management Firm)

We need a website designed. We have attached a Powerpoint with our proposed website content (which is quite minimal), the format is just a suggestion but we would like to see your alternative and improved ideas. We are a boutique investment firm so are looking for something sleek and professional. I have included on the last page of the attachment our brand colours and font styles as well as attaching our logo design. We would like the successful designer to design the website and build the buttons etc.

On the "Contact Us" page, we are open to suggestions on how best to show the map, whether is should be static or open a google maps page. We would like the phone number and email address to be set up so people can click on them on their phone and it calls us or emails us directly.

We would prefer not to have photos of landscapes on the site.
Our website is hosted on a Linux based website.

We would also like 3 links at the bottom of each page for links to pdfs:
- Disclaimer, Terms and Conditions of Web Site Use
- Stewardship
- Pillar III

Target Market(s)

Institutional Investors

Industry/Entity Type

Investment

Coding

Coded - Design and coding required

Number of Pages Required

3 page

Font styles to use
Other font styles liked:
• Logo: Lato, Text: Source Sans Pro

Colors

Designer to choose colors to be used in the design.

Requirements
Must have
• The website must use the colours and fonts on the last page of the attached powerpoint. I can't see an option to select the exact colour palette below so please look at the PPT.
• For others please see Project description.
Should not have
• Landscape photos

```html
<!DOCTYPE html>
<html lang="en">
<head>
<meta charset="utf-8">
<title>Norvane Investment Management</title>
<link href="https://fonts.googleapis.com/css2?family=Lato:wght@400;700&family=Open+Sans:wght@400&display=swap" rel="stylesheet">
<style>
  :root {
    --hero-deep: #24487a;
    --hero-mid: #34598c;
    --hero-light: #4a6f9c;
    --white: #ffffff;
    --footer-bg: #2a2a2a;
    --footer-text: #f2f2f2;
  }
  * { margin: 0; padding: 0; box-sizing: border-box; }
  html, body { width: 1200px; height: 840px; overflow: hidden; }
  body { font-family: 'Open Sans', sans-serif; color: var(--white); background: var(--footer-bg); }

  .hero { position: relative; width: 1200px; height: 670px; overflow: hidden; }
  .hero-backdrop {
    position: absolute; inset: 0;
    background:
      radial-gradient(ellipse 520px 380px at 300px 330px, rgba(80,115,160,0.55), transparent 70%),
      radial-gradient(ellipse 420px 340px at 880px 470px, rgba(95,130,175,0.45), transparent 70%),
      linear-gradient(160deg, var(--hero-light) 0%, var(--hero-mid) 45%, var(--hero-deep) 100%);
  }

  .brand { position: absolute; left: 99px; top: 45px; display: flex; align-items: center; gap: 12px; }
  .brand-mark { width: 52px; height: 52px; background: var(--white); }
  .brand-text { display: flex; flex-direction: column; }
  .brand-name { font-family: 'Lato', sans-serif; font-weight: 400; font-size: 42px; line-height: 40px; letter-spacing: 1px; }
  .brand-tagline { font-family: 'Lato', sans-serif; font-size: 9px; letter-spacing: 2.2px; text-transform: uppercase; margin-top: 4px; }

  .main-nav { position: absolute; top: 56px; right: 99px; display: flex; gap: 6px; }
  .nav-item {
    position: relative; height: 36px; padding: 0 22px;
    border: 1px solid var(--white);
    font-family: 'Lato', sans-serif; font-size: 17px; line-height: 34px;
    color: var(--white); text-decoration: none;
  }
  .nav-item.is-active::after {
    content: ""; position: absolute; left: 50%; bottom: -8px;
    width: 12px; height: 12px; margin-left: -6px;
    border-right: 1px solid var(--white); border-bottom: 1px solid var(--white);
    background: var(--hero-mid); transform: rotate(45deg);
  }

  .welcome { position: absolute; top: 266px; left: 0; width: 1200px; text-align: center; }
  .welcome-title { font-family: 'Lato', sans-serif; font-weight: 700; font-size: 48px; line-height: 60px; }
  .welcome-lead { font-family: 'Lato', sans-serif; font-size: 14.5px; line-height: 21px; width: 620px; margin: 14px auto 0; }
  .welcome-body { font-size: 11.5px; line-height: 20.5px; width: 670px; margin: 16px auto 0; }

  .slider-dots { position: absolute; top: 566px; left: 563px; display: flex; align-items: center; gap: 7px; }
  .dot { width: 10px; height: 10px; border-radius: 50%; background: var(--white); }
  .dot.is-current { width: 20px; height: 20px; border: 1.5px solid var(--white); background: transparent; display: flex; align-items: center; justify-content: center; margin-right: 1px; }
  .dot.is-current::before { content: ""; width: 11px; height: 11px; border-radius: 50%; background: var(--white); }

  .site-footer { position: relative; height: 170px; background: var(--footer-bg); color: var(--footer-text); text-align: center; }
  .footer-links { padding-top: 45px; font-size: 13px; }
  .footer-links a { color: var(--footer-text); text-decoration: none; }
  .footer-links .sep { margin: 0 8px; }
  .copyright { margin-top: 14px; font-size: 11.5px; }
  .version { position: absolute; right: 32px; top: 78px; font-size: 11.5px; }
  .social { display: flex; justify-content: center; gap: 4px; margin-top: 17px; }
  .social-link { width: 27px; height: 27px; border: 1.5px solid var(--white); border-radius: 50%; }
</style>
</head>
<body>
  <header class="hero">
    <div class="hero-backdrop" role="img" aria-label="Blue-toned photo of a person at a laptop reviewing printed financial charts"></div>

    <div class="brand">
      <div class="brand-mark"></div>
      <div class="brand-text">
        <span class="brand-name">NORVANE</span>
        <span class="brand-tagline">Investment Management</span>
      </div>
    </div>

    <nav class="main-nav">
      <a class="nav-item is-active" href="#">About Norvane</a>
      <a class="nav-item" href="#">Our Approach and Philosophy</a>
      <a class="nav-item" href="#">Contact Us</a>
    </nav>

    <section class="welcome">
      <h1 class="welcome-title">Welcome to Norvane</h1>
      <p class="welcome-lead">Norvane Investment Management was founded in 2016 with a clear vision to create an independent and nimble firm focused on generating superior risk-adjusted returns.</p>
      <p class="welcome-body">Norvane has designed an innovative investment approach which aims to harness the best elements of alternative investment management whilst reducing its recognised shortcomings. We are a performance and client focused firm, committed to building lasting relationships, treating our clients like partners rather than revenue streams.</p>
    </section>

    <div class="slider-dots">
      <span class="dot is-current"></span>
      <span class="dot"></span>
      <span class="dot"></span>
      <span class="dot"></span>
    </div>
  </header>

  <footer class="site-footer">
    <nav class="footer-links">
      <a href="#">Home</a><span class="sep">/</span>
      <a href="#">Disclaimer</a><span class="sep">/</span>
      <a href="#">Terms and Conditions</a><span class="sep">/</span>
      <a href="#">Stewardship</a><span class="sep">/</span>
      <a href="#">Pillar III</a>
    </nav>
    <p class="copyright">Copyright @ 2017 Norvane Investment Management. All Rights Reserved.</p>
    <span class="version">C7</span>
    <div class="social">
      <a class="social-link" href="#" aria-label="Social profile"></a>
      <a class="social-link" href="#" aria-label="Social profile"></a>
      <a class="social-link" href="#" aria-label="Social profile"></a>
      <a class="social-link" href="#" aria-label="Social profile"></a>
      <a class="social-link" href="#" aria-label="Social profile"></a>
    </div>
  </footer>
</body>
</html>
```